Corporate Business Card

Very professional, Modern, Not to busy, include phone address email, website
(253) 617-4930, 18761 52nd Avenue S, Kent, WA 98047, martin@plumlinegroup.com, varkoworks.com

Target Market(s)

Manufacturing

Industry/Entity Type

Aero, machining, manufacturing, Off road racing

Contact Information for Business Card

Phone, address email, website

```html
<!DOCTYPE html>
<html lang="en">
<head>
<meta charset="utf-8">
<title>Varko Works — Business Card</title>
<link href="https://fonts.googleapis.com/css2?family=Montserrat:wght@500;600;700&display=swap" rel="stylesheet">
<style>
  :root {
    --navy: #163370;
    --red: #d8202c;
    --white: #ffffff;
    --silver: #c7cad1;
    --ink: #1a1a1a;
    --backdrop: #ece9e4;
  }
  * { box-sizing: border-box; margin: 0; padding: 0; }
  html, body {
    width: 1200px; height: 1023px; overflow: hidden;
    background: var(--backdrop);
    font-family: "Montserrat", sans-serif;
  }
  .card {
    position: absolute;
    width: 540px; height: 309px;
    border-radius: 22px;
    overflow: hidden;
    box-shadow: 0 10px 28px rgba(0,0,0,0.18);
  }
  .card-front { left: 80px; top: 130px; background: var(--navy); }
  .card-back { left: 580px; top: 570px; background: var(--white); }

  .front-brand {
    position: absolute; left: 0; right: 0; top: 112px;
    text-align: center;
    color: var(--silver);
    font-weight: 700; font-size: 58px; letter-spacing: 1px;
  }
  .front-rule {
    position: absolute; left: 120px; width: 300px; top: 210px;
    height: 2px; background: var(--silver);
  }

  .back-swoosh { position: absolute; inset: 0; width: 100%; height: 100%; }
  .back-brand {
    position: absolute; right: 42px; top: 46px;
    display: flex; align-items: center; gap: 10px;
    color: var(--navy); font-weight: 700; font-size: 36px;
  }
  .back-brand .mark { width: 16px; height: 16px; background: var(--red); }
  .back-rule {
    position: absolute; right: 90px; top: 108px;
    width: 230px; height: 2px; background: var(--navy);
  }
  .address {
    position: absolute; left: 40px; top: 112px;
    font-size: 15px; font-weight: 500; line-height: 1.45; color: var(--ink);
  }
  .contacts {
    position: absolute; left: 40px; top: 178px;
    list-style: none; font-size: 14px; font-weight: 500; color: var(--ink);
  }
  .contacts li { display: flex; align-items: center; gap: 10px; height: 23px; }
  .contacts svg { width: 14px; height: 14px; fill: var(--red); flex: none; }
</style>
</head>
<body>

<section class="card card-front">
  <div class="front-brand">Varko Works</div>
  <div class="front-rule"></div>
</section>

<section class="card card-back">
  <svg class="back-swoosh" viewBox="0 0 540 309" preserveAspectRatio="none" aria-hidden="true">
    <path d="M0,309 L0,300 C330,302 500,222 540,60 L540,309 Z" fill="var(--navy)"/>
    <path d="M0,288 C330,291 502,208 532,72 C505,216 330,297 0,294 Z" fill="var(--red)"/>
  </svg>

  <div class="back-brand"><span class="mark"></span>Varko Works</div>
  <div class="back-rule"></div>

  <p class="address">18761 52nd Avenue<br>S, Kent, WA 98047</p>

  <ul class="contacts">
    <li>
      <svg viewBox="0 0 24 24"><path d="M6.6 10.8a15 15 0 0 0 6.6 6.6l2.2-2.2a1 1 0 0 1 1-.25 11.4 11.4 0 0 0 3.6.57 1 1 0 0 1 1 1V20a1 1 0 0 1-1 1A17 17 0 0 1 3 4a1 1 0 0 1 1-1h3.5a1 1 0 0 1 1 1c0 1.25.2 2.45.57 3.57a1 1 0 0 1-.25 1z"/></svg>
      (253) 617-4930
    </li>
    <li>
      <svg viewBox="0 0 24 24"><path d="M2 5h20v14H2z"/><path d="M3 6l9 7 9-7" fill="none" stroke="#fff" stroke-width="1.5"/></svg>
      martin@plumlinegroup.com
    </li>
    <li>
      <svg viewBox="0 0 24 24"><circle cx="12" cy="12" r="10"/><path d="M2 12h20M12 2c3 3 3 17 0 20M12 2c-3 3-3 17 0 20" fill="none" stroke="#fff" stroke-width="1.3"/></svg>
      www.varkoworks.com
    </li>
  </ul>
</section>

</body>
</html>
```